deceased estate clean ups brochures

we would like a brochure to reresent our business we already have new web site and want to do DL A4 brochure to give out to promote our business we already have logo www.brightmoor.com.au is where you can get all info needed

Target Market(s)

families with loved ones that have past away
people done sizing or needing to decluter

Colors
cadf82
33b8a4
886aae
33a6d7

```html
<!DOCTYPE html>
<html lang="en">
<head>
<meta charset="utf-8">
<title>Brightmoor – Trifold Brochure Inside</title>
<link href="https://fonts.googleapis.com/css2?family=Saira+Condensed:wght@600;700&family=PT+Sans+Narrow:wght@400;700&display=swap" rel="stylesheet">
<style>
  :root{
    --purple:#886aae;
    --purple-deep:#5f3f8a;
    --purple-light:#a48cc6;
    --teal:#33b8a4;
    --teal-deep:#2aa58f;
    --green:#0a9a3c;
    --green-light:#12a84c;
    --green-dark:#067a2c;
    --panel-grey:#efefef;
    --ink:#4a4a4a;
    --ink-dark:#1e1e1e;
    --white:#ffffff;
    --heading:"Saira Condensed", sans-serif;
    --body:"PT Sans Narrow", sans-serif;
  }
  *{box-sizing:border-box;margin:0;padding:0}
  html,body{width:1200px;height:1080px;overflow:hidden;background:#e6e6e6}
  .brochure{position:relative;width:1200px;height:1080px;display:flex}
  .panel{position:relative;width:400px;height:1080px;overflow:hidden}
  .panel svg.shapes{position:absolute;inset:0;width:400px;height:1080px}

  /* Left panel */
  .panel--why{background:var(--white)}
  .panel--why h2{position:absolute;left:28px;top:78px;font-family:var(--heading);font-weight:700;font-size:30px;color:var(--white);letter-spacing:.3px}
  .why-copy{position:absolute;left:28px;top:280px;width:350px;font-family:var(--body);font-size:13.5px;line-height:21px;color:var(--ink)}
  .why-copy p{margin-bottom:18px}
  .brand-word{color:var(--purple);font-size:15px}
  .photo-couple{position:absolute;left:0;top:700px;width:400px;height:380px;background:linear-gradient(160deg,#d9c9bd,#b6a39a 55%,#8f8aa6);clip-path:polygon(0 70px,400px 55px,400px 380px,0 380px)}

  /* Centre panel */
  .panel--services{background:var(--panel-grey)}
  .services-title{position:absolute;left:48px;top:20px;width:300px;height:70px;background:var(--teal);display:flex;align-items:center;justify-content:center;font-family:var(--heading);font-weight:700;font-size:34px;color:var(--white)}
  .service-photo{position:absolute;left:0;width:400px;height:210px;border-left:12px solid var(--teal)}
  .service-photo--cleaning{top:112px;background:linear-gradient(120deg,#e8e2da,#c9b9a4 50%,#55627a)}
  .service-photo--moving{top:460px;background:linear-gradient(120deg,#c7b7a3,#7c8aa2 45%,#e9ecef)}
  .service-heading{position:absolute;left:0;width:400px;text-align:center;font-family:var(--heading);font-weight:700;font-size:28px;color:var(--purple)}
  .service-heading::after{content:"";display:block;width:210px;height:3px;background:var(--teal);margin:2px auto 0}
  .service-heading--cleaning{top:336px}
  .service-heading--prep{top:680px;font-size:24px}
  .service-heading--prep::after{width:230px}
  .service-text{position:absolute;left:16px;width:368px;text-align:center;font-family:var(--body);font-size:12.5px;line-height:16px;color:var(--ink)}
  .service-text--cleaning{top:386px}
  .service-text--prep{top:730px}

  /* Right panel */
  .panel--process{background:linear-gradient(180deg,var(--green-light),var(--green) 50%,var(--green-dark))}
  .process-title{position:absolute;left:20px;top:50px;font-family:var(--heading);font-weight:700;font-size:44px;color:var(--white);line-height:1}
  .process-rule{position:absolute;left:76px;top:112px;width:218px;height:6px;background:var(--white)}
  .steps{position:absolute;left:20px;top:180px;width:362px;font-family:var(--body);color:var(--white);font-size:13.5px;line-height:18px}
  .step{margin-bottom:14px}
  .step h3{font-family:var(--heading);font-weight:700;font-size:22px;line-height:1.1;margin-bottom:4px}
  .checklist{list-style:none}
  .checklist li{display:flex;gap:6px;margin-bottom:10px}
  .checklist svg{flex:0 0 16px;width:16px;height:16px;margin-top:1px}
  .brand-name{position:absolute;left:0;width:400px;top:965px;text-align:center;font-family:var(--heading);font-weight:700;font-size:44px;letter-spacing:2px;color:var(--ink-dark)}
</style>
</head>
<body>
<main class="brochure">

  <section class="panel panel--why">
    <svg class="shapes" viewBox="0 0 400 1080" aria-hidden="true">
      <defs>
        <linearGradient id="whyBand" x1="0" x2="1">
          <stop offset="0" stop-color="#8467ad"/><stop offset="1" stop-color="#a48cc6"/>
        </linearGradient>
      </defs>
      <polygon points="0,0 400,0 400,140 0,232" fill="url(#whyBand)"/>
      <polygon points="0,232 400,140 0,262" fill="#33b8a4"/>
    </svg>
    <h2>WHY CHOOSE US</h2>
    <div class="why-copy">
      <p>At <span class="brand-word">Brightmoor</span> our goal is to ease your worries and help you with your journey in preparing your house for rental or resale.</p>
      <p>Whether it is a move to another residence or the difficult task with dealing with the grief when a loved one passes away, <span class="brand-word">Brightmoor</span> can help with the preparation of the property for sale. Brightmoor will come in, remove unwanted items and dispose of all rubbish, do cosmetic repairs if required and leave the property in a spotless state.</p>
      <p>Our trained and reliable staff, repair any house and carry out landscaping in preparation for renting or resale of the property in a timely and professional manner. Our team provides a discrete and trustworthy service, keeping in mind the sensitive nature of the work.</p>
      <p><span class="brand-word">Brightmoor</span> will make sure that all remaining furniture and possessions left inside the property are removed/sold/taken to storage and the remainder of unwanted goods are sorted so that the entire property is completely cleared for rental or sale.</p>
    </div>
    <div class="photo-couple" role="img" aria-label="Photo of a smiling older couple reviewing paperwork at home"></div>
  </section>

  <section class="panel panel--services">
    <div class="services-title">SERVICES OFFERED</div>
    <div class="service-photo service-photo--cleaning" role="img" aria-label="Photo of a cleaning crew wiping and mopping a living room"></div>
    <h3 class="service-heading service-heading--cleaning">CLEANING SERVICE</h3>
    <p class="service-text service-text--cleaning">We can provide a Cleaning Service for a house sale or rental preparation or a deceased estate. Houses need to be cleared for the property market, but they...</p>
    <div class="service-photo service-photo--moving" role="img" aria-label="Photo of a couple moving furniture and boxes in a bright room"></div>
    <h3 class="service-heading service-heading--prep">PREPARATION FOR RENTAL OR SALE</h3>
    <p class="service-text service-text--prep">Our target is to create maximum appeal on all aspects of your property, allowing you to sell or rent and attract a higher sale price when</p>
    <svg class="shapes" viewBox="0 0 400 1080" aria-hidden="true">
      <polygon points="0,996 400,858 400,880 0,1034" fill="#33b8a4"/>
      <polygon points="0,1034 400,880 400,1080 0,1080" fill="#7d5fa5"/>
    </svg>
  </section>

  <section class="panel panel--process">
    <svg class="shapes" viewBox="0 0 400 1080" aria-hidden="true">
      <defs>
        <linearGradient id="processBand" x1="0" x2="1">
          <stop offset="0" stop-color="#5f3f8a"/><stop offset="1" stop-color="#886aae"/>
        </linearGradient>
      </defs>
      <polygon points="0,838 400,700 400,716 0,862" fill="#2aa58f"/>
      <polygon points="0,862 400,716 400,1080 0,1080" fill="url(#processBand)"/>
    </svg>
    <h2 class="process-title">OUR 5 STEP PROCESS</h2>
    <div class="process-rule"></div>
    <div class="steps">
      <div class="step">
        <h3>STEP 1:</h3>
        <p>We start with a consultation at the property, understanding our client's needs, requests and priorities. Create a plan of what needs to be done in each step of your move. Provide a personalized quote.</p>
      </div>
      <div class="step">
        <h3>STEP 2:</h3>
        <p>Pre-sale decluttering and sorting of items. Unwanted items to be sold, given to friends, family or charity.</p>
      </div>
      <div class="step">
        <h3>STEP 3:</h3>
        <ul class="checklist">
          <li><svg viewBox="0 0 16 16"><rect x="1" y="3" width="12" height="12" fill="none" stroke="#fff" stroke-width="1.5"/><path d="M3 9l3 3 9-11" fill="none" stroke="#fff" stroke-width="2.2"/></svg><span>We thoroughly clear and clean the property (inside and outside) prior to sale or rent.</span></li>
          <li><svg viewBox="0 0 16 16"><rect x="1" y="3" width="12" height="12" fill="none" stroke="#fff" stroke-width="1.5"/><path d="M3 9l3 3 9-11" fill="none" stroke="#fff" stroke-width="2.2"/></svg><span>House to be staged and set up to enhance its presentation for sale or rent.</span></li>
          <li><svg viewBox="0 0 16 16"><rect x="1" y="3" width="12" height="12" fill="none" stroke="#fff" stroke-width="1.5"/><path d="M3 9l3 3 9-11" fill="none" stroke="#fff" stroke-width="2.2"/></svg><span>Rubbish to be picked up.</span></li>
          <li><svg viewBox="0 0 16 16"><rect x="1" y="3" width="12" height="12" fill="none" stroke="#fff" stroke-width="1.5"/><path d="M3 9l3 3 9-11" fill="none" stroke="#fff" stroke-width="2.2"/></svg><span>Garden to be tidied.</span></li>
          <li><svg viewBox="0 0 16 16"><rect x="1" y="3" width="12" height="12" fill="none" stroke="#fff" stroke-width="1.5"/><path d="M3 9l3 3 9-11" fill="none" stroke="#fff" stroke-width="2.2"/></svg><span>After settlement, we begin to pack your possessions ready to be moved as directed.</span></li>
        </ul>
      </div>
      <div class="step">
        <h3>STEP 4:</h3>
        <p>Organising and arranging transport of your possessions.</p>
      </div>
      <div class="step">
        <h3>STEP 5:</h3>
        <p>Storage or unpacking your possessions and setting up as per your instructions.</p>
      </div>
    </div>
    <div class="brand-name">BRIGHTMOOR</div>
  </section>

</main>
</body>
</html>
```